TalkHarbor - Language Coaching Services

Sleek, innovative, trendy design for Language Coaching business.

TalkHarbor is a new UK based company that provides Language Coaching services. We offer highly personalized on-line and face to face language courses. We also impart learning techniques workshops based on the latest neuroscience research for second-language acquisition.

Target Market(s)

See attached info

Industry/Entity Type

Consulting

Contact Information for Business Card

TalkHarbor
DaniaKV@talkharbor.co.uk
TalkHarbor.co.uk
London, UK

Font styles to use
Sans Serif

```html
<!DOCTYPE html>
<html lang="en">
<head>
<meta charset="utf-8">
<title>TalkHarbor Business Card</title>
<link href="https://fonts.googleapis.com/css2?family=Lato:wght@400;700&family=Montserrat:wght@400;600&display=swap" rel="stylesheet">
<style>
  :root {
    --backdrop: #4f4f4f;
    --brand-light: #00a3df;
    --brand-dark: #076ca2;
    --brand-mid: #1a8fc7;
    --paper: #ffffff;
    --faint: #eaf4fa;
    --ink-light: #ffffff;
  }
  html, body {
    margin: 0;
    padding: 0;
    width: 1200px;
    height: 802px;
    overflow: hidden;
    background: var(--backdrop);
  }
  .canvas {
    position: relative;
    width: 1200px;
    height: 802px;
  }
  .card {
    position: absolute;
    top: 234px;
    width: 560px;
    height: 334px;
    overflow: hidden;
    box-shadow: 0 4px 10px rgba(0,0,0,0.35);
  }
  .card--back { left: 25px; background: var(--brand-dark); }
  .card--front { left: 615px; background: var(--paper); }

  .emblem-area {
    position: absolute;
    top: 0;
    left: 0;
    height: 100%;
  }
  .card--back .emblem-area {
    width: 215px;
    background: linear-gradient(90deg, var(--brand-light) 0%, var(--brand-light) 75%, #0a8cc6 100%);
  }
  .card--front .emblem-area {
    width: 230px;
    background: linear-gradient(90deg, var(--faint) 0%, var(--faint) 70%, rgba(234,244,250,0) 100%);
  }

  .contact {
    position: absolute;
    right: 25px;
    top: 84px;
    text-align: right;
    color: var(--ink-light);
    font-family: "Lato", sans-serif;
    font-size: 15.5px;
    line-height: 20px;
  }
  .contact__name {
    font-family: "Montserrat", sans-serif;
    font-weight: 600;
    font-size: 20px;
    line-height: 22px;
    letter-spacing: 0.2px;
  }
  .contact__role { margin-bottom: 19px; }
  .contact__city { margin-bottom: 21px; }
  .contact__line {
    display: flex;
    justify-content: flex-end;
    align-items: center;
    gap: 3px;
  }
  .contact__line svg { width: 12px; height: 12px; flex: none; }

  .brand-mark {
    position: absolute;
    left: 221px;
    top: 85px;
    width: 118px;
    height: 118px;
    box-sizing: border-box;
    border: 5px solid var(--brand-mid);
    border-radius: 50%;
  }
  .brand-name {
    position: absolute;
    left: 0;
    width: 100%;
    top: 208px;
    text-align: center;
    font-family: "Montserrat", sans-serif;
    font-weight: 600;
    font-size: 44px;
    letter-spacing: 1px;
    color: var(--brand-mid);
    margin: 0;
  }
</style>
</head>
<body>
<main class="canvas">
  <section class="card card--back">
    <div class="emblem-area" role="img" aria-label="Brand emblem decoration in light blue"></div>
    <div class="contact">
      <div class="contact__name">MARCUS REED</div>
      <div class="contact__role">Managing Director</div>
      <div class="contact__city">London, UK</div>
      <div class="contact__line">044 777 1234
        <svg viewBox="0 0 12 12" aria-hidden="true"><rect x="2" y="0.8" width="8" height="10.4" rx="1.2" fill="none" stroke="#fff" stroke-width="1.4"/><rect x="5" y="9" width="2" height="1" fill="#fff"/></svg>
      </div>
      <div class="contact__line">DaniaKV@talkharbor.co.uk
        <svg viewBox="0 0 12 12" aria-hidden="true"><rect x="0.5" y="2.5" width="11" height="7.5" fill="#fff"/><path d="M0.8 2.8 L6 7 L11.2 2.8" fill="none" stroke="#076ca2" stroke-width="1"/></svg>
      </div>
      <div class="contact__line">www.TalkHarbor.co.uk
        <svg viewBox="0 0 12 12" aria-hidden="true"><circle cx="6" cy="6" r="5.5" fill="#fff"/><path d="M3 3.5 Q5 3 5.5 5 Q4 6.5 5 8.5 M8 2.5 Q7 5 9.5 6" fill="none" stroke="#076ca2" stroke-width="1"/></svg>
      </div>
    </div>
  </section>

  <section class="card card--front">
    <div class="emblem-area" role="img" aria-label="Faint brand emblem decoration"></div>
    <div class="brand-mark" aria-hidden="true"></div>
    <h1 class="brand-name">TALKHARBOR</h1>
  </section>
</main>
</body>
</html>
```